Luxury Wine Label for New Startup Winery

We need a wine label for our new winery startup. We have worked with a local designer but do not feel the resulting label / logo have the elevation required to present our brand as a luxury wine. Our winery is called "Quailbrook Vineyards" and we are focused on extremely high quality hand crafted artisan and estate wines from the Pacific Northwest.
We would like to see designs that utilize a tree line, or other imagery that represents the "Quailbrook" part of our company name. Another interesting feature could be wood grain.
A logo will be required based on your design so please design with this in mind:
This logo should be consistent with the wine bottle label design, and should be representative of our high end exclusive wine while giving a sense of place (Oregon/ Pacific Northwest.)
I will supply an image of the design we received from our local designer, PLEASE NOTE: in general we do like wood grain and tree line concepts but feel the execution was poorly done.
ATTN: Logo design should be suitable for use on: Bottles (Red wine/rose/white wine), Bussiness cards, vehicle signage, business signage, etc
P.S.:
If you have a design that is not outside the box we are still interested in seeing it.
Label is for a burgundy style bottle with a label height of 3.5 - 4" and a width of 3.5-4"
any label <= 4"x4" and >=3.5"x3.5" will be acceptable:
HOWEVER Width should be greater than or equal to height due to the bottle format
Target Market(s)
Wine enthusiasts with adequate discretionary budgets to afford $100 bottles of wine.
Industry/Entity Type
Wine / Winery
Requirements
Must have
- A sense of luxury, a feel of exclusivity, and a theme consistent with our product and brand name
Nice to have
- Tree line, wood grain or other wood themes. Serif fonts
Should not have
- anything cheesy, off topic, hard to read script fonts or anything that makes the label hard to read from a few feet away or too busy

```html
<!DOCTYPE html>
<html lang="en">
<head>
<meta charset="utf-8">
<title>Quailbrook Vineyards — Syrah Label</title>
<link rel="stylesheet" href="https://fonts.googleapis.com/css2?family=Cinzel:wght@400;500&family=Roboto+Slab:wght@600;700&display=swap">
<style>
  :root {
    --page: #ffffff;
    --label-black: #1c1c1c;
    --ink-white: #ffffff;
    --gold: #c9a13a;
    --gold-light: #f3e07a;
    --gold-deep: #b88d2a;
    --silver-dark: #6f6f6f;
    --silver-light: #f4f4f4;
    --wood-dark: #3a2517;
    --wood-mid: #6b4a33;
    --ink-dark: #2a2015;
  }
  * { margin: 0; padding: 0; box-sizing: border-box; }
  html, body {
    width: 1134px; height: 1200px; overflow: hidden;
    background: var(--page);
  }
  .canvas { position: relative; width: 1134px; height: 1200px; }

  .front-label {
    position: absolute; left: 16px; top: 16px; width: 1098px; height: 889px;
    background: var(--label-black);
  }
  .silver-band {
    position: absolute; left: 0; width: 100%; height: 33px;
    background: linear-gradient(90deg, var(--silver-dark) 0%, #d8d8d8 18%, var(--silver-light) 50%, #d8d8d8 80%, var(--silver-dark) 100%);
  }
  .silver-band.top { top: 0; }
  .silver-band.bottom { bottom: 0; height: 35px; }
  .gold-stripe {
    position: absolute; left: 0; width: 100%; height: 15px;
    background: linear-gradient(90deg, var(--gold-deep), var(--gold) 50%, var(--gold-deep));
  }
  .gold-stripe.upper { top: 804px; }
  .gold-stripe.lower { top: 830px; }

  .brand-mark {
    position: absolute; left: 359px; top: 103px; width: 380px; height: 380px;
  }
  .brand-name {
    position: absolute; left: 0; width: 100%; text-align: center;
    font-family: "Cinzel", serif; font-weight: 400; color: var(--ink-white);
  }
  .brand-name.primary { top: 510px; font-size: 70px; letter-spacing: 4px; }
  .brand-name.secondary { top: 590px; font-size: 52px; letter-spacing: 8px; }
  .region {
    position: absolute; left: 0; top: 700px; width: 100%; text-align: center;
    font-family: "Roboto Slab", serif; font-weight: 600; font-size: 36px;
    letter-spacing: 4px; color: var(--gold);
  }

  .varietal-label {
    position: absolute; left: 16px; top: 941px; width: 1098px; height: 241px;
  }
  .gold-band {
    position: absolute; left: 0; width: 100%;
    background: linear-gradient(90deg, var(--gold-deep) 0%, var(--gold-light) 45%, var(--gold-light) 60%, var(--gold-deep) 100%);
  }
  .gold-band.top { top: 0; height: 21px; }
  .gold-band.bottom { bottom: 0; height: 35px; }
  .wood-panel {
    position: absolute; left: 0; top: 21px; width: 100%; height: 185px;
    background: linear-gradient(180deg, var(--wood-mid) 0%, var(--wood-dark) 40%, var(--wood-mid) 70%, var(--wood-dark) 100%);
  }
  .varietal {
    position: absolute; left: 0; top: 72px; width: 100%; text-align: center;
    font-family: "Cinzel", serif; font-weight: 400; font-size: 84px;
    letter-spacing: 6px; color: var(--ink-white); line-height: 1;
  }
  .vintage-line {
    position: absolute; left: 0; bottom: 0; width: 100%; height: 35px;
    line-height: 35px; text-align: center;
    font-family: "Roboto Slab", serif; font-weight: 700; font-size: 20px;
    letter-spacing: 4px; color: var(--ink-dark);
  }
</style>
</head>
<body>
<main class="canvas">
  <section class="front-label">
    <div class="silver-band top"></div>

    <svg class="brand-mark" viewBox="0 0 380 380" aria-hidden="true">
      <circle cx="190" cy="190" r="180" fill="none" stroke="#ffffff" stroke-width="12"/>
    </svg>

    <h1 class="brand-name primary">QUAILBROOK</h1>
    <p class="brand-name secondary">VINEYARDS</p>
    <p class="region">“WILLAMETTE VALLEY”</p>

    <div class="gold-stripe upper"></div>
    <div class="gold-stripe lower"></div>
    <div class="silver-band bottom"></div>
  </section>

  <section class="varietal-label">
    <div class="gold-band top"></div>
    <div class="wood-panel" role="img" aria-label="Dark walnut wood grain texture"></div>
    <h2 class="varietal">SYRAH</h2>
    <div class="gold-band bottom"></div>
    <p class="vintage-line">ESTATE | 2023 | GROWN</p>
  </section>
</main>
</body>
</html>
```